Austin TX First Veterinary Urgent Care

We need a flyer designed for us and our clinic that is eye-catching but also summarizes the advantages of our services. We want to express that we are family owned, have convenient hours and affordable prices. We are the first veterinary urgent care animal clinic in Austin Texas. Our hours of operation are M-F 12PM-9PM S-S 10AM-6PM. Our Address is 4871 W Larkspur Rd Suite B212 Austin, Tx 78753. Our phone number is (737)555-0148 our website is www.brookpawclinic.com and our email address is info@brookpawclinic.com.

Target Market(s)

Pet owners and veterinary professionals for referral purposes.

Industry/Entity Type

Veterinary

Font styles to use
Sans Serif

Colors
0094D4
00A9DD
6FCCEA
C7EBF8
E9F6FB
00AB8E
00BBA5
67D7C9
C6EFE9
E9F9F6

Requirements
Must have
• Our logo, hours of operation and contact information easy to read. Should emphasize that we are affordable as well as family owned. List of services should also be displayed: ear, eye, and skin issues, limping, broken toenails, lacerations, coughing, sneezing, allergies, vomiting and diarrhea, urinary issues, constipation, snake bites, toxin ingestion, and many many more
Nice to have
• We would like to have a modern feel with drawn/cartoon images, not realistic stock photos of dogs/cats.

```html
<!DOCTYPE html>
<html lang="en">
<head>
<meta charset="utf-8">
<title>BrookPaw Vet – Veterinary Urgent Care Flyer</title>
<link href="https://fonts.googleapis.com/css2?family=Poppins:wght@400;500;600;700;800&display=swap" rel="stylesheet">
<style>
:root{
  --navy:#14148a;
  --navy-bright:#2323d6;
  --green:#45ad55;
  --ink:#222222;
  --grey:#8a8a8a;
  --paper:#ffffff;
  --backdrop:#d9dade;
}
*{margin:0;padding:0;box-sizing:border-box}
html,body{width:1200px;height:2333px;overflow:hidden;background:var(--backdrop)}
body{position:relative;font-family:"Poppins",sans-serif;color:var(--ink)}
.flyer{
  position:absolute;left:50px;top:454px;width:728px;height:943px;
  background:var(--paper);transform:scale(1.511);transform-origin:0 0;
  box-shadow:0 6px 18px rgba(0,0,0,.18);overflow:hidden;
}
.abs{position:absolute}
.brand{left:48px;top:52px;display:flex;align-items:center;gap:12px}
.brand-dot{width:44px;height:44px;border-radius:50%;background:var(--green)}
.brand-name{font-size:40px;font-weight:800;color:var(--navy);line-height:1;white-space:nowrap}
.headline{left:46px;top:150px;white-space:nowrap}
.headline div{white-space:nowrap}
.headline .l1{font-size:36.5px;font-weight:800;color:var(--navy);line-height:1.05;letter-spacing:.2px}
.headline .l2{font-size:53px;font-weight:800;color:var(--green);line-height:.98}
.headline .l3{font-size:33px;font-weight:500;color:var(--navy);letter-spacing:8.6px;line-height:1.1}
.intro{left:46px;top:283px;width:345px;font-size:14px;line-height:1.25}
.afford-icon{left:46px;top:345px}
.afford{left:115px;top:344px;color:var(--navy);white-space:nowrap}
.afford .a1{font-size:29px;font-weight:400;line-height:1.05}
.afford .a1 b{font-weight:700}
.afford .a2{font-size:21px;font-weight:500;line-height:1.1}
.services-title{left:46px;top:428px;font-size:27px;font-weight:500;color:var(--navy);white-space:nowrap}
.services-title b{font-weight:700}
.services-rule{left:44px;top:470px}
.svc-col{top:488px;list-style:none}
.svc-col li{display:flex;align-items:flex-start;gap:10px;font-size:17px;font-weight:500;line-height:1.2;margin-bottom:11.5px;white-space:nowrap}
.svc-col li svg{flex:none;margin-top:3px}
.svc-left{left:46px}
.svc-right{left:254px;width:180px}
.svc-divider{left:232px;top:490px;width:1px;height:255px;background:#cfcfcf}
.more{left:254px;top:730px;font-size:13px;white-space:nowrap}
.contact-bar{left:46px;top:781px;width:312px;height:26px;color:#fff;font-size:13px;padding-left:14px;line-height:26px;
  background:linear-gradient(110deg,var(--navy) 0 60%,var(--navy-bright) 60% 100%)}
.contact{left:46px;list-style:none;font-size:14.5px}
.contact li{display:flex;align-items:center;gap:14px;height:28px;white-space:nowrap}
.art-team{left:405px;top:45px;width:316px;height:290px}
.art-exam{left:420px;top:352px;width:304px;height:350px}
.call{left:452px;top:703px;width:236px;text-align:center;font-size:15.5px;white-space:nowrap}
.frame{left:450px;top:727px}
.phone{left:450px;top:733px;width:235px;text-align:center;font-size:29px;font-weight:700;color:var(--navy);line-height:1.1}
.clinic{left:450px;top:768px;width:235px;text-align:center;font-size:23px;line-height:1}
.shelter{left:450px;top:790px;width:235px;text-align:center;font-size:37px;font-weight:500;line-height:1;letter-spacing:.5px}
.hours-rule{left:450px;top:823px;width:234px;height:2px;background:var(--green)}
.hours{left:450px;top:830px;width:234px;height:113px;background:var(--green);color:#fff;font-size:11.5px;font-weight:700;text-align:center;padding-top:20px;line-height:26px;white-space:nowrap}
</style>
</head>
<body>
<main class="flyer">
  <div class="abs brand"><span class="brand-dot"></span><span class="brand-name">BrookPaw Vet</span></div>

  <h1 class="abs headline">
    <div class="l1">AUSTIN TX FIRST</div>
    <div class="l2">VETERINARY</div>
    <div class="l3">URGENT CARE</div>
  </h1>
  <p class="abs intro">We are the first veterinary urgent care animal clinic in Austin Texas.</p>

  <svg class="abs afford-icon" width="56" height="58" viewBox="0 0 56 58">
    <path d="M16 0h14v16h16v14H30v16H16V30H0V16h16z" fill="#b9b9b9"/>
    <circle cx="42" cy="44" r="12" fill="var(--green)" stroke="#fff" stroke-width="2"/>
  </svg>
  <div class="abs afford">
    <div class="a1">We are <b>Affordable</b></div>
    <div class="a2">as well as family owned.</div>
  </div>

  <h2 class="abs services-title">LIST OF <b>SERVICES</b></h2>
  <svg class="abs services-rule" width="370" height="4"><rect x="0" y="0" width="30" height="3" fill="var(--navy)"/><rect x="42" y="0" width="328" height="3" fill="var(--navy)"/></svg>

  <ul class="abs svc-col svc-left">
    <li><svg width="16" height="14" viewBox="0 0 16 14"><g fill="#6b6b6b"><ellipse cx="8" cy="10" rx="4" ry="3.4"/><circle cx="2.5" cy="6" r="1.7"/><circle cx="5.5" cy="2.5" r="1.7"/><circle cx="10.5" cy="2.5" r="1.7"/><circle cx="13.5" cy="6" r="1.7"/></g></svg>Ear</li>
    <li><svg width="16" height="14" viewBox="0 0 16 14"><g fill="#6b6b6b"><ellipse cx="8" cy="10" rx="4" ry="3.4"/><circle cx="2.5" cy="6" r="1.7"/><circle cx="5.5" cy="2.5" r="1.7"/><circle cx="10.5" cy="2.5" r="1.7"/><circle cx="13.5" cy="6" r="1.7"/></g></svg>Eye</li>
    <li><svg width="16" height="14" viewBox="0 0 16 14"><g fill="#6b6b6b"><ellipse cx="8" cy="10" rx="4" ry="3.4"/><circle cx="2.5" cy="6" r="1.7"/><circle cx="5.5" cy="2.5" r="1.7"/><circle cx="10.5" cy="2.5" r="1.7"/><circle cx="13.5" cy="6" r="1.7"/></g></svg>Skin Issues</li>
    <li><svg width="16" height="14" viewBox="0 0 16 14"><g fill="#6b6b6b"><ellipse cx="8" cy="10" rx="4" ry="3.4"/><circle cx="2.5" cy="6" r="1.7"/><circle cx="5.5" cy="2.5" r="1.7"/><circle cx="10.5" cy="2.5" r="1.7"/><circle cx="13.5" cy="6" r="1.7"/></g></svg>Limping</li>
    <li><svg width="16" height="14" viewBox="0 0 16 14"><g fill="#6b6b6b"><ellipse cx="8" cy="10" rx="4" ry="3.4"/><circle cx="2.5" cy="6" r="1.7"/><circle cx="5.5" cy="2.5" r="1.7"/><circle cx="10.5" cy="2.5" r="1.7"/><circle cx="13.5" cy="6" r="1.7"/></g></svg>Broken Toenails</li>
    <li><svg width="16" height="14" viewBox="0 0 16 14"><g fill="#6b6b6b"><ellipse cx="8" cy="10" rx="4" ry="3.4"/><circle cx="2.5" cy="6" r="1.7"/><circle cx="5.5" cy="2.5" r="1.7"/><circle cx="10.5" cy="2.5" r="1.7"/><circle cx="13.5" cy="6" r="1.7"/></g></svg>Lacerations</li>
    <li><svg width="16" height="14" viewBox="0 0 16 14"><g fill="#6b6b6b"><ellipse cx="8" cy="10" rx="4" ry="3.4"/><circle cx="2.5" cy="6" r="1.7"/><circle cx="5.5" cy="2.5" r="1.7"/><circle cx="10.5" cy="2.5" r="1.7"/><circle cx="13.5" cy="6" r="1.7"/></g></svg>Coughing</li>
    <li><svg width="16" height="14" viewBox="0 0 16 14"><g fill="#6b6b6b"><ellipse cx="8" cy="10" rx="4" ry="3.4"/><circle cx="2.5" cy="6" r="1.7"/><circle cx="5.5" cy="2.5" r="1.7"/><circle cx="10.5" cy="2.5" r="1.7"/><circle cx="13.5" cy="6" r="1.7"/></g></svg>Sneezing</li>
  </ul>
  <div class="abs svc-divider"></div>
  <ul class="abs svc-col svc-right">
    <li><svg width="16" height="14" viewBox="0 0 16 14"><g fill="#6b6b6b"><ellipse cx="8" cy="10" rx="4" ry="3.4"/><circle cx="2.5" cy="6" r="1.7"/><circle cx="5.5" cy="2.5" r="1.7"/><circle cx="10.5" cy="2.5" r="1.7"/><circle cx="13.5" cy="6" r="1.7"/></g></svg>Allergies</li>
    <li><svg width="16" height="14" viewBox="0 0 16 14"><g fill="#6b6b6b"><ellipse cx="8" cy="10" rx="4" ry="3.4"/><circle cx="2.5" cy="6" r="1.7"/><circle cx="5.5" cy="2.5" r="1.7"/><circle cx="10.5" cy="2.5" r="1.7"/><circle cx="13.5" cy="6" r="1.7"/></g></svg>Vomiting and<br>Diarrhea</li>
    <li><svg width="16" height="14" viewBox="0 0 16 14"><g fill="#6b6b6b"><ellipse cx="8" cy="10" rx="4" ry="3.4"/><circle cx="2.5" cy="6" r="1.7"/><circle cx="5.5" cy="2.5" r="1.7"/><circle cx="10.5" cy="2.5" r="1.7"/><circle cx="13.5" cy="6" r="1.7"/></g></svg>Urinary Issues</li>
    <li><svg width="16" height="14" viewBox="0 0 16 14"><g fill="#6b6b6b"><ellipse cx="8" cy="10" rx="4" ry="3.4"/><circle cx="2.5" cy="6" r="1.7"/><circle cx="5.5" cy="2.5" r="1.7"/><circle cx="10.5" cy="2.5" r="1.7"/><circle cx="13.5" cy="6" r="1.7"/></g></svg>Constipation</li>
    <li><svg width="16" height="14" viewBox="0 0 16 14"><g fill="#6b6b6b"><ellipse cx="8" cy="10" rx="4" ry="3.4"/><circle cx="2.5" cy="6" r="1.7"/><circle cx="5.5" cy="2.5" r="1.7"/><circle cx="10.5" cy="2.5" r="1.7"/><circle cx="13.5" cy="6" r="1.7"/></g></svg>Snake Bites</li>
    <li><svg width="16" height="14" viewBox="0 0 16 14"><g fill="#6b6b6b"><ellipse cx="8" cy="10" rx="4" ry="3.4"/><circle cx="2.5" cy="6" r="1.7"/><circle cx="5.5" cy="2.5" r="1.7"/><circle cx="10.5" cy="2.5" r="1.7"/><circle cx="13.5" cy="6" r="1.7"/></g></svg>Toxin ingestion</li>
  </ul>
  <p class="abs more">&amp; many many more......</p>

  <div class="abs contact-bar">CONTACT INFORMATION</div>
  <ul class="abs contact" style="top:818px">
    <li><svg width="20" height="20" viewBox="0 0 20 20"><circle cx="10" cy="10" r="10" fill="var(--green)"/><path d="M10 4a4 4 0 0 0-4 4c0 3 4 8 4 8s4-5 4-8a4 4 0 0 0-4-4z" fill="#fff"/><circle cx="10" cy="8" r="1.5" fill="var(--green)"/></svg>4871 W Larkspur Rd Suite B212 Austin, Tx 78753</li>
    <li><svg width="20" height="20" viewBox="0 0 20 20"><circle cx="10" cy="10" r="10" fill="var(--green)"/><rect x="5" y="6.5" width="10" height="7" fill="#fff"/><path d="M5 6.5l5 4 5-4" fill="none" stroke="var(--green)" stroke-width="1.2"/></svg>info@brookpawclinic.com</li>
    <li><svg width="20" height="20" viewBox="0 0 20 20"><circle cx="10" cy="10" r="10" fill="var(--green)"/><g fill="none" stroke="#fff" stroke-width="1.2"><circle cx="10" cy="10" r="5.5"/><ellipse cx="10" cy="10" rx="2.4" ry="5.5"/><path d="M4.5 10h11"/></g></svg>www.brookpawclinic.com</li>
  </ul>

  <svg class="abs art-team" viewBox="0 0 316 290" role="img" aria-label="Cartoon illustration of a smiling veterinarian waving with a dog, a cat and a puppy">
    <defs><linearGradient id="teamFade" x1="0" y1="0" x2="0" y2="1"><stop offset="0" stop-color="#8e8e8e"/><stop offset="1" stop-color="#f4f4f4"/></linearGradient></defs>
    <path d="M40 70C60 20 130 0 190 12c60 10 110 50 120 110 8 55-20 105-75 125-50 18-120 30-175 5C15 230-5 180 10 140c8-25 20-45 30-70z" fill="url(#teamFade)"/>
  </svg>
  <svg class="abs art-exam" viewBox="0 0 304 350" role="img" aria-label="Cartoon illustration of a veterinarian examining a dog on a table beside a supply shelf, with a cat and dogs nearby">
    <defs><linearGradient id="examFade" x1="0" y1="0" x2="0" y2="1"><stop offset="0" stop-color="#f2f4f5"/><stop offset=".5" stop-color="#dfe3e6"/><stop offset="1" stop-color="#e8d3bd"/></linearGradient></defs>
    <rect x="0" y="0" width="304" height="350" rx="14" fill="url(#examFade)"/>
  </svg>

  <p class="abs call">Call us to make appointment</p>
  <svg class="abs frame" width="236" height="88" viewBox="0 0 236 88">
    <path d="M40 86H1V1h234v85h-28" fill="none" stroke="var(--navy)" stroke-width="2"/>
  </svg>
  <div class="abs phone">737-555-0148</div>
  <div class="abs clinic">Animal Clinic</div>
  <div class="abs shelter">SHELTER</div>
  <div class="abs hours-rule"></div>
  <div class="abs hours">MONDAY TO FRIDAY 12PM TO 9PM<br>SATURDAY TO SUNDAY 10AM TO 6PM</div>
</main>
</body>
</html>
```